Card Design Project

A simple, funky, cool birth announcement card
Not corporate, but arty
Not childish nor girlish
No baby pictures

Text is tbc (eg name and date may change)

Front side: just the name "fenna"
Should be easy to read

Back side text (in Dutch):

We vinden je nu al leuk!

20 JUNE 2013
Singapore

Dochter van Marieke Dorrel & Joost Vermalen

Yangon, Myanmar
+95 1 64 8319
Skype: Marieke.Dorrel
Skype: Joost.Vermalen

Size will be A6
Updates

Reason: Dear designers, At this stage we would like to have one or more designers to draft up the card (of which the final text is still tbd as the baby is yet to be born) using the typeface used on the left below (or similar!) of the newly added picture - in black - in fluorescent colours Can you get back to us in a few days? Thanks

Target Market(s)

Our funky friends in holland.

Industry/Entity Type

Baby

Requirements
Must have
• Colours, aswe are very happy to welcome this baby.
Something that makes it stand out from all other baby birth announcement cards

A6 size
Deadline 21 June
Printing will be on white (thick paper 250g)
Design for 5mm "bleedsides" all around
At least available in PDF (and other formats)
Nice to have
• We've recently moved from netherlands to Yangon
We could include the iconic kyauktaran pagoda

I would like for it to look like a cool party announcement

Include bright fluoriscent colours, including orange.
The enveloppe will be orange
Should not have
• Any baby stuff, soft pink dominance, childish stuff.

```html
<!DOCTYPE html>
<html lang="nl">
<head>
<meta charset="utf-8">
<title>Geboortekaart Fenna</title>
<link rel="stylesheet" href="https://fonts.googleapis.com/css2?family=Quicksand:wght@700&display=swap">
<style>
  :root {
    --card-w: 1200px;
    --card-h: 866px;
    --text-yellow: #f3e12b;
    --panel-navy: #1f3a4b;
    --panel-navy-deep: #17303f;
    --lime: #9be81c;
    --green: #2f8a1e;
    --ray-yellow: #f6f35a;
    --ray-cyan: #7ee7d6;
    --burst-orange: #f0771f;
    --burst-blue: #1f3fb0;
    --name-top: #ffe640;
    --name-bottom: #f7a21a;
    --name-edge: #e4561c;
  }
  html, body {
    margin: 0;
    padding: 0;
    width: var(--card-w);
    height: var(--card-h);
    overflow: hidden;
    background: #ffffff;
  }
  .card {
    position: relative;
    width: var(--card-w);
    height: var(--card-h);
    overflow: hidden;
    font-family: "Quicksand", "Arial Rounded MT Bold", sans-serif;
    font-weight: 700;
  }
  .edge-art {
    position: absolute;
    top: 0;
    left: 0;
    width: 148px;
    height: 100%;
    background:
      linear-gradient(180deg, rgba(155,232,28,.9) 0%, rgba(47,138,30,.85) 30%, rgba(155,232,28,.9) 55%, rgba(47,138,30,.9) 80%, rgba(155,232,28,.85) 100%);
  }
  .text-panel {
    position: absolute;
    top: 0;
    left: 148px;
    width: 594px;
    height: 100%;
    background: linear-gradient(160deg, var(--panel-navy) 0%, var(--panel-navy-deep) 60%, var(--panel-navy) 100%);
  }
  .burst-art {
    position: absolute;
    top: 0;
    left: 742px;
    width: 458px;
    height: 100%;
    background:
      radial-gradient(ellipse 55% 45% at 63% 70%, rgba(240,119,31,.95) 0%, rgba(240,119,31,0) 70%),
      radial-gradient(circle at 25% 33%, var(--ray-yellow) 0%, var(--lime) 25%, var(--ray-cyan) 50%, rgba(31,63,176,.9) 85%, var(--burst-blue) 100%);
  }
  .info {
    position: absolute;
    left: 193px;
    margin: 0;
    color: var(--text-yellow);
    line-height: 1.42;
  }
  .greeting { top: 100px; font-size: 24px; }
  .birth { top: 264px; font-size: 30px; line-height: 43px; }
  .parents { top: 376px; font-size: 30px; line-height: 44px; }
  .contact { top: 600px; font-size: 30px; line-height: 41px; }
  .info span { display: block; }
  .baby-name {
    position: absolute;
    left: 780px;
    top: 660px;
    width: 400px;
    height: 120px;
  }
</style>
</head>
<body>
<main class="card">
  <div class="edge-art" role="img" aria-label="Groene grunge-textuur met lichtstralen"></div>
  <div class="text-panel"></div>
  <div class="burst-art" role="img" aria-label="Fluorescerende zonnestralen-illustratie in geel, groen, oranje en blauw met grunge-textuur"></div>

  <p class="info greeting">We vinden je nu al leuk!</p>

  <p class="info birth">
    <span>20 JUNE 2013</span>
    <span>Singapore</span>
  </p>

  <p class="info parents">
    <span>Dochter van</span>
    <span>Marieke Dorrel &amp; Joost Vermalen</span>
  </p>

  <p class="info contact">
    <span>Yangon, Myanmar</span>
    <span>+95 1 64 8319</span>
    <span>Skype: Marieke.Dorrel</span>
    <span>Skype: Joost.Vermalen</span>
  </p>

  <svg class="baby-name" viewBox="0 0 400 120" aria-label="FENNA">
    <defs>
      <linearGradient id="name-fill" x1="0" y1="0" x2="0" y2="1">
        <stop offset="0" stop-color="var(--name-top)"/>
        <stop offset="1" stop-color="var(--name-bottom)"/>
      </linearGradient>
    </defs>
    <text x="4" y="106" textLength="390" lengthAdjust="spacingAndGlyphs"
          font-family="Quicksand, sans-serif" font-weight="700" font-size="128"
          fill="url(#name-fill)" stroke="var(--name-edge)" stroke-width="3"
          paint-order="stroke">FENNA</text>
  </svg>
</main>
</body>
</html>
```